Corvane Capital Business Cards

These are professional business cards that are for my family office.
Put fake emails and phone numbers as of now until I finalize those components. This family office controls my families investments, assets, and future. The cards should be professional.
..
.
.
.
I just uploaded another variation of a logo I would like to see as a business card to I am inbeteen which logo to use

Target Market(s)

business

Industry/Entity Type

business

Contact Information for Business Card

Professional, wealth related, finance related.

Requirements
Must have
• Logo

```html
<!DOCTYPE html>
<html lang="en">
<head>
<meta charset="utf-8">
<title>Corvane Capital Business Cards</title>
<link href="https://fonts.googleapis.com/css2?family=Tinos:wght@400;700&display=swap" rel="stylesheet">
<style>
  :root {
    --navy: #1c2e57;
    --navy-faint: #2f4170;
    --yellow: #ffed00;
    --ink: #231f20;
    --slate: #5a5b5a;
    --white: #ffffff;
    --page: #ffffff;
  }
  * { box-sizing: border-box; margin: 0; padding: 0; }
  html, body { width: 1200px; height: 1200px; overflow: hidden; background: var(--page); }
  .canvas { position: relative; width: 1200px; height: 1200px; }

  .card {
    position: absolute;
    left: 280px;
    width: 648px;
    height: 369px;
    background: var(--navy);
    border-radius: 16px;
    overflow: hidden;
    box-shadow: 9px 9px 10px rgba(0,0,0,0.45);
    font-family: "Tinos", "Times New Roman", serif;
  }
  .card--front { top: 217px; }
  .card--back { top: 621px; }

  .brand-name {
    position: absolute;
    font-family: "Tinos", "Times New Roman", serif;
    font-weight: 400;
    color: var(--white);
    white-space: nowrap;
    text-align: center;
  }
  .front-brand-name { left: 0; width: 330px; top: 162px; font-size: 28px; }
  .back-brand-name { left: 0; width: 648px; top: 160px; font-size: 38px; }

  .decor-name {
    position: absolute;
    font-family: "Tinos", "Times New Roman", serif;
    font-size: 20px;
    color: var(--navy-faint);
    white-space: nowrap;
  }

  .divider {
    position: absolute;
    left: 355px; top: 58px;
    width: 2px; height: 131px;
    background: var(--white);
    border-radius: 1px;
  }

  .row {
    position: absolute;
    left: 386px;
    width: 262px;
    display: flex;
  }
  .row__icon {
    width: 51px;
    height: 100%;
    background: var(--ink);
    display: flex; align-items: center; justify-content: center;
  }
  .row__body {
    flex: 1;
    background: var(--white);
    color: var(--ink);
    font-size: 12px;
    padding-left: 27px;
    display: flex; align-items: center;
  }

  .holder { top: 51px; height: 41px; }
  .holder .row__body {
    background: var(--slate);
    flex-direction: column;
    align-items: flex-start;
    justify-content: center;
    line-height: 1;
  }
  .holder__name { font-size: 20px; color: var(--white); }
  .holder__first { color: var(--ink); font-weight: 700; }
  .holder__role { font-size: 12px; color: var(--white); margin-top: 1px; }

  .contact--phone { top: 131px; height: 28px; }
  .contact--email { top: 172px; height: 28px; }
  .contact--web { top: 213px; height: 28px; }

  .address {
    position: absolute;
    left: 469px; top: 287px;
    display: flex; align-items: center; gap: 14px;
    color: var(--white);
    font-size: 12px;
    line-height: 1.05;
  }

  .tab {
    position: absolute;
    top: 108px;
    width: 41px; height: 154px;
    background: var(--yellow);
  }
  .tab--left { left: 0; border-radius: 0 5px 5px 0; }
  .tab--right { right: 0; border-radius: 5px 0 0 5px; }
</style>
</head>
<body>
<main class="canvas">

  <section class="card card--front" aria-label="Front of business card">
    <div class="decor-name" style="left:16px;top:40px;">Corvane Capital</div>
    <div class="decor-name" style="left:16px;top:330px;">Corvane Capital</div>
    <div class="decor-name" style="left:215px;top:280px;">Corvane Capital</div>

    <div class="brand-name front-brand-name">Corvane Capital</div>

    <div class="divider"></div>

    <div class="row holder">
      <div class="row__icon">
        <svg width="24" height="34" viewBox="0 0 24 34" aria-hidden="true">
          <circle cx="12" cy="7" r="6" fill="#fff"/>
          <path d="M1 33 V22 Q1 15 8 15 H16 Q23 15 23 22 V33 Z" fill="#fff"/>
          <path d="M10 15 L12 22 L14 15 Z" fill="#231f20"/>
        </svg>
      </div>
      <div class="row__body">
        <span class="holder__name"><span class="holder__first">Rafael</span> Moreno</span>
        <span class="holder__role">Manager</span>
      </div>
    </div>

    <div class="row contact--phone">
      <div class="row__icon">
        <svg width="18" height="18" viewBox="0 0 24 24" aria-hidden="true">
          <path d="M6.6 10.8a15 15 0 0 0 6.6 6.6l2.2-2.2a1 1 0 0 1 1-.25 11.4 11.4 0 0 0 3.6.57 1 1 0 0 1 1 1V20a1 1 0 0 1-1 1A17 17 0 0 1 3 4a1 1 0 0 1 1-1h3.5a1 1 0 0 1 1 1c0 1.25.2 2.45.57 3.57a1 1 0 0 1-.25 1z" fill="none" stroke="#fff" stroke-width="1.8"/>
          <path d="M14 3a7 7 0 0 1 7 7M14 6.5a3.5 3.5 0 0 1 3.5 3.5" fill="none" stroke="#fff" stroke-width="1.8"/>
        </svg>
      </div>
      <div class="row__body">0145 027 0189</div>
    </div>

    <div class="row contact--email">
      <div class="row__icon">
        <svg width="18" height="14" viewBox="0 0 18 14" aria-hidden="true">
          <rect x="1" y="1" width="16" height="12" fill="none" stroke="#fff" stroke-width="1.4"/>
          <path d="M1 1 L9 8 L17 1 M1 13 L7 6.5 M17 13 L11 6.5" fill="none" stroke="#fff" stroke-width="1.4"/>
        </svg>
      </div>
      <div class="row__body">hello@corvanemail.com</div>
    </div>

    <div class="row contact--web">
      <div class="row__icon">
        <svg width="18" height="18" viewBox="0 0 18 18" aria-hidden="true">
          <circle cx="8" cy="8" r="7" fill="none" stroke="#fff" stroke-width="1.4"/>
          <ellipse cx="8" cy="8" rx="3" ry="7" fill="none" stroke="#fff" stroke-width="1.2"/>
          <path d="M1 8 H15 M2.5 4.5 H13.5 M2.5 11.5 H13.5" stroke="#fff" stroke-width="1.2"/>
          <path d="M10 9 L10 17 L12 15 L13.5 18 L15 17.3 L13.5 14.5 L16 14.3 Z" fill="#fff" stroke="#231f20" stroke-width="0.8"/>
        </svg>
      </div>
      <div class="row__body">www.corvanecapital.com</div>
    </div>

    <div class="address">
      <svg width="20" height="18" viewBox="0 0 20 18" aria-hidden="true">
        <path d="M2 9 L10 2 L18 9" fill="none" stroke="#fff" stroke-width="2.2" stroke-linejoin="round"/>
        <path d="M4 8 V17 H16 V8" fill="none" stroke="#fff" stroke-width="2"/>
        <rect x="8" y="11" width="4" height="6" fill="#fff"/>
        <rect x="14" y="2" width="2" height="4" fill="#fff"/>
      </svg>
      <p>Your location<br>Harbor Street, Eastbay,<br>1000.</p>
    </div>
  </section>

  <section class="card card--back" aria-label="Back of business card">
    <div class="tab tab--left"></div>
    <div class="tab tab--right"></div>
    <div class="brand-name back-brand-name">Corvane Capital</div>
  </section>

</main>
</body>
</html>
```